Brell Stone Company Business Cards

Front and Back Business Card - logo and text setup - cool design. I need workable photoshop or illustrator files so I can setup each employee card with design that is created
Updates

Hi everyone, thank you for the great entries. Please no more white and blue cards - there are so many already - black and silver only now please. thanks!

Target Market(s)

Construction Industry - Facility Managers

Industry/Entity Type

Construction

Contact Information for Business Card

I really like contemporary simplistic looks - clean neat....not opposed to seeing some black backrounds

Requirements
Must have
• Logo/website address with design on front only - www.brellstone-example.com (logo attached)
• Back:
• Name/Title/Company Address/Phone/email address
Nice to have
• Cool design
Should not have
• Nothing gimmicky like Fire or Water - since we are a Fire Protection company - it has all been done

```html
<!DOCTYPE html>
<html lang="en">
<head>
<meta charset="UTF-8">
<title>Brell Stone Company – Business Cards</title>
<link href="https://fonts.googleapis.com/css2?family=Work+Sans:wght@400;500;700&display=swap" rel="stylesheet">
<style>
  :root {
    --bg: #141414;
    --card: #232323;
    --card-edge: #2c2c2c;
    --silver: #d9d9d9;
    --silver-soft: #b9b9b9;
    --rule: #8a8a8a;
  }
  * { margin: 0; padding: 0; box-sizing: border-box; }
  html, body {
    width: 1200px; height: 900px; overflow: hidden;
    background: var(--bg);
    font-family: "Work Sans", Arial, sans-serif;
  }
  .sheet {
    width: 1200px; height: 900px;
    display: flex; flex-direction: column; align-items: center; justify-content: center;
    gap: 44px;
  }
  .card {
    width: 620px; height: 354px;
    background: linear-gradient(160deg, var(--card-edge), var(--card));
    border-radius: 2px;
    position: relative;
    box-shadow: 0 14px 30px rgba(0,0,0,.55);
  }
  .wordmark {
    color: var(--silver);
    font-weight: 700;
    letter-spacing: -0.5px;
    line-height: 1.05;
  }
  .card--front { display: flex; align-items: center; justify-content: center; }
  .card--front .wordmark { font-size: 46px; text-align: center; }
  .card--back { display: flex; align-items: center; padding: 0 34px 0 40px; }
  .card--back .wordmark { font-size: 34px; width: 230px; }
  .divider {
    width: 1px; height: 228px; background: var(--rule);
    margin: 0 28px 0 24px;
  }
  .details { color: var(--silver); }
  .details__name { font-size: 21px; font-weight: 500; letter-spacing: 1px; }
  .details__title { font-size: 14px; color: var(--silver-soft); letter-spacing: 1px; margin-top: 2px; }
  .details__address { font-size: 14px; letter-spacing: 1px; line-height: 1.45; margin-top: 20px; }
  .contact-list { list-style: none; margin-top: 12px; font-size: 14px; letter-spacing: 1px; }
  .contact-list li { display: flex; align-items: center; gap: 10px; line-height: 1.65; }
  .contact-list svg { width: 11px; height: 11px; fill: none; stroke: var(--silver-soft); stroke-width: 1.4; flex: none; }
</style>
</head>
<body>
<main class="sheet">
  <section class="card card--front" aria-label="Card front">
    <div class="wordmark">Brell Stone<br>Company</div>
  </section>

  <section class="card card--back" aria-label="Card back">
    <div class="wordmark">Brell Stone<br>Company</div>
    <div class="divider"></div>
    <div class="details">
      <div class="details__name">DANIEL WARD</div>
      <div class="details__title">Director</div>
      <div class="details__address">48 Harbor Point Road<br>Millbrook, NY 10000</div>
      <ul class="contact-list">
        <li>
          <svg viewBox="0 0 12 12"><path d="M3 1 L5 3.5 L4 5 Q5 7 7 8 L8.5 7 L11 9 L10 11 Q4 10.5 1.5 2.5 Z"/></svg>
          (555) 014-2290
        </li>
        <li>
          <svg viewBox="0 0 12 12"><rect x="3" y="1" width="6" height="3"/><rect x="1" y="4" width="10" height="4.5"/><rect x="3" y="7" width="6" height="4"/></svg>
          (555) 014-2291
        </li>
        <li>
          <svg viewBox="0 0 12 12"><rect x="1" y="2.5" width="10" height="7"/><path d="M1 2.5 L6 6.5 L11 2.5"/></svg>
          info@brellstone-example.com
        </li>
        <li>
          <svg viewBox="0 0 12 12"><circle cx="6" cy="6" r="5"/><ellipse cx="6" cy="6" rx="2.2" ry="5"/><path d="M1 6 H11"/></svg>
          www.brellstone-example.com
        </li>
      </ul>
    </div>
  </section>
</main>
</body>
</html>
```